plumbRIDGE corporation pty ltd

Contruction industry
It's a wall and floor tiling business

Industry/Entity Type

Business

Requirements
Must have
• Likes-
- clean and easy to read
- a witty design is always well received
- for it to look reputable in the industry
- a strong and direct presentation
- simple but striking colour selection
Should not have
• Dislikes-
- pls no tacky square tiles to resemble tiling

```html
<!DOCTYPE html>
<html lang="en">
<head>
<meta charset="utf-8">
<title>Plumbridge Corporation Pty Ltd – business card</title>
<link href="https://fonts.googleapis.com/css2?family=Arimo:wght@400&display=swap" rel="stylesheet">
<style>
  :root {
    --backdrop: #e9e9ec;
    --card-blue: #0b2d96;
    --card-blue-deep: #082478;
    --ink-white: #ffffff;
    --rule: rgba(255,255,255,0.55);
  }
  * { margin: 0; padding: 0; box-sizing: border-box; }
  html, body {
    width: 1200px; height: 1023px; overflow: hidden;
    background: var(--backdrop);
    font-family: "Arimo", Arial, sans-serif;
  }
  .sheet {
    position: relative; width: 1200px; height: 1023px;
    display: flex; flex-direction: column; align-items: center; justify-content: center;
    gap: 44px;
  }
  .card {
    position: relative; width: 820px; height: 468px;
    border-radius: 22px;
    background: linear-gradient(160deg, var(--card-blue) 0%, var(--card-blue) 60%, var(--card-blue-deep) 100%);
    color: var(--ink-white);
    box-shadow: 0 10px 26px rgba(0,0,0,0.18);
    overflow: hidden;
  }

  /* company name: one colour, one weight, one size */
  .company-name {
    position: absolute;
    font-weight: 400;
    line-height: 1.1;
    white-space: nowrap;
    text-align: left;
  }
  .company-name__line { display: block; }

  .card--front .company-name { left: 110px; top: 160px; font-size: 64px; }
  .card--back .company-name { left: 56px; top: 60px; font-size: 46px; }

  .person { position: absolute; left: 150px; top: 268px; }
  .person__name { font-size: 58px; font-weight: 400; line-height: 1; white-space: nowrap; }
  .person__role { font-size: 18px; text-align: right; margin-top: 6px; }

  .divider {
    position: absolute; left: 500px; top: 228px; width: 1.5px; height: 138px;
    background: linear-gradient(to bottom, transparent, var(--rule), transparent);
  }

  .contacts { position: absolute; left: 528px; top: 264px; list-style: none; }
  .contacts__item { display: flex; align-items: center; gap: 12px; font-size: 19px; margin-bottom: 18px; white-space: nowrap; }
  .contacts__icon { width: 22px; height: 22px; flex: none; }

  .edge-line {
    position: absolute; left: 0; right: 0; bottom: 26px; height: 3px;
    background: var(--ink-white);
  }
</style>
</head>
<body>
  <main class="sheet">
    <section class="card card--back" aria-label="Business card, contact side">
      <p class="company-name">
        <span class="company-name__line">Plumbridge</span>
        <span class="company-name__line">Corporation Pty Ltd</span>
      </p>
      <div class="person">
        <p class="person__name">Dan Merrow</p>
        <p class="person__role">Director</p>
      </div>
      <div class="divider"></div>
      <ul class="contacts">
        <li class="contacts__item">
          <svg class="contacts__icon" viewBox="0 0 24 24" aria-hidden="true">
            <path d="M6.6 3.5 9.3 3l1.4 4.3-1.9 1.4a11 11 0 0 0 6.5 6.5l1.4-1.9 4.3 1.4-.5 2.7c-.2 1-1 1.6-2 1.6A15.4 15.4 0 0 1 3 5.5c0-1 .6-1.8 1.6-2Z" fill="#ffffff"/>
          </svg>
          <span>0400 555 018</span>
        </li>
        <li class="contacts__item">
          <svg class="contacts__icon" viewBox="0 0 24 24" aria-hidden="true">
            <rect x="2" y="5" width="20" height="14" rx="2" fill="#ffffff"/>
            <path d="M3 6.5 12 13l9-6.5" fill="none" stroke="#0b2d96" stroke-width="1.8"/>
          </svg>
          <span>dan.merrow@mailbox.com</span>
        </li>
      </ul>
      <div class="edge-line"></div>
    </section>

    <section class="card card--front" aria-label="Business card, brand side">
      <p class="company-name">
        <span class="company-name__line">Plumbridge</span>
        <span class="company-name__line">Corporation Pty Ltd</span>
      </p>
    </section>
  </main>
</body>
</html>
```